Brightmill Data Works

Our company is about IT hardwares and IT solutions. IT hardware such as PC, RAMS, storage and servers. IT solutions such as project management, BA. We are also selling new technology too.

Target Market(s)

Consumer, Small to Medium Business, Corporate

Requirements
Must have
• The business card must have the following:
• Name:
• Title:
• Contact Number:
• Email address:
• Website:
• Color: Must match the logo color upgrade

```html
<!DOCTYPE html>
<html lang="en">
<head>
<meta charset="utf-8">
<title>Brightmill Data Works — Business Card</title>
<link rel="stylesheet" href="https://fonts.googleapis.com/css2?family=Oswald:wght@500&family=Work+Sans:wght@400;500;700&display=swap">
<style>
  :root {
    --stage: #161616;
    --card: #262626;
    --card-edge: #303030;
    --ink-light: #f2f2f2;
    --ink-mute: #bdbdbd;
    --accent: #e8a23a;
  }
  * { box-sizing: border-box; margin: 0; padding: 0; }
  html, body {
    width: 1200px; height: 900px; overflow: hidden;
    background: var(--stage);
  }
  .canvas {
    position: relative; width: 1200px; height: 900px;
    background: radial-gradient(ellipse at 50% 40%, #222 0%, var(--stage) 70%);
  }
  .card {
    position: absolute; left: 280px; width: 640px; height: 366px;
    background: linear-gradient(135deg, var(--card) 0%, #2c2c2c 60%, var(--card) 100%);
    border: 1px solid var(--card-edge);
    box-shadow: 0 18px 40px rgba(0,0,0,.55);
  }
  .card--front { top: 60px; display: flex; align-items: center; justify-content: center; }
  .card--back { top: 474px; }

  .wordmark {
    display: flex; align-items: center; gap: 16px;
    font-family: "Work Sans", sans-serif; font-weight: 700;
    font-size: 36px; letter-spacing: 1px; text-transform: uppercase;
    color: var(--ink-mute); white-space: nowrap;
  }
  .wordmark__dot { width: 22px; height: 22px; background: var(--ink-mute); }

  .identity {
    position: absolute; left: 70px; top: 130px; width: 250px; text-align: right;
  }
  .identity__name {
    font-family: "Oswald", sans-serif; font-weight: 500;
    font-size: 34px; line-height: 1; color: var(--accent);
    text-transform: uppercase; white-space: nowrap;
  }
  .identity__title {
    margin-top: 6px;
    font-family: "Work Sans", sans-serif; font-size: 16px; color: var(--ink-light);
  }
  .divider {
    position: absolute; left: 338px; top: 132px; width: 2px; height: 64px;
    background: var(--ink-light);
  }
  .contacts {
    position: absolute; left: 358px; top: 128px; list-style: none;
    font-family: "Work Sans", sans-serif; font-size: 16px; color: var(--ink-light);
    white-space: nowrap;
  }
  .contacts li { display: flex; align-items: center; gap: 10px; height: 24px; }
  .contacts svg { width: 13px; height: 13px; flex: none; }
  .contacts .accent { color: var(--accent); }
  .address {
    position: absolute; left: 100px; bottom: 46px;
    font-family: "Work Sans", sans-serif; font-size: 17px; color: var(--ink-light);
    white-space: nowrap;
  }
</style>
</head>
<body>
<main class="canvas">
  <section class="card card--front">
    <div class="wordmark">
      <span class="wordmark__dot"></span>
      <span>Brightmill Data Works</span>
    </div>
  </section>

  <section class="card card--back">
    <div class="identity">
      <p class="identity__name">Daniel Harrow</p>
      <p class="identity__title">Director</p>
    </div>
    <div class="divider"></div>
    <ul class="contacts">
      <li>
        <svg viewBox="0 0 16 16" aria-hidden="true"><path d="M4 1 L6.5 1 L7.5 4.5 L5.8 5.8 Q7 9 10.2 10.2 L11.5 8.5 L15 9.5 L15 12 Q14.5 15 11 14.5 Q2 12 1.5 5 Q1 1.5 4 1 Z" fill="var(--accent)"/></svg>
        <span>555-204-7731</span>
      </li>
      <li>
        <svg viewBox="0 0 16 16" aria-hidden="true"><rect x="1" y="3" width="14" height="10" fill="none" stroke="var(--accent)" stroke-width="1.6"/><path d="M1 3 L8 9 L15 3" fill="none" stroke="var(--accent)" stroke-width="1.6"/></svg>
        <span>info@brightmilldata.com</span>
      </li>
      <li>
        <svg viewBox="0 0 16 16" aria-hidden="true"><g fill="none" stroke="var(--accent)" stroke-width="1.4"><circle cx="8" cy="8" r="6.5"/><ellipse cx="8" cy="8" rx="3" ry="6.5"/><path d="M1.5 8 H14.5 M2.5 4.8 H13.5 M2.5 11.2 H13.5"/></g></svg>
        <span>www.<span class="accent">brightmilldata</span>.com</span>
      </li>
    </ul>
    <p class="address">820 Alder Creek Way Fairview, CA 94120-3307</p>
  </section>
</main>
</body>
</html>
```